Upmarket Dessert Lounge needs a Business Card Design

We are an upmarket dessert lounge needing a business card to match our image.

We want something that is simple yet beautiful, feminine, classy, sophisticated and elegant. We want it to stand out and don't mind if it is bold.

The design should include our logo and colours of red or maroon with gold highlights. We don't mind if black is used.

Marlow & Quince

Target Market(s)

For those who like to indulge or treat themselves and give in to their temptations on good quality desserts.

Industry/Entity Type

Business

Requirements
Must have
• Must include our logo and our name

Marlow & Quince

M & Q

```html
<!DOCTYPE html>
<html lang="en">
<head>
<meta charset="utf-8">
<title>Marlow &amp; Quince — Business Card</title>
<link rel="stylesheet" href="https://fonts.googleapis.com/css2?family=Cinzel:wght@400;700&family=Tinos&display=swap">
<style>
  :root {
    --backdrop: #e8e3da;
    --navy: #0b1128;
    --maroon: #7a1515;
    --gold: #f1d7a2;
    --gold-soft: #e6c98f;
    --divider: rgba(241, 215, 162, 0.45);
  }
  * { box-sizing: border-box; margin: 0; padding: 0; }
  html, body {
    width: 1200px;
    height: 417px;
    overflow: hidden;
    background: var(--backdrop);
  }
  .canvas {
    position: relative;
    width: 1200px;
    height: 417px;
  }
  .card {
    position: absolute;
    top: 62px;
    width: 515px;
    height: 293px;
    background: var(--navy);
    border-radius: 14px;
    overflow: hidden;
    box-shadow: 0 3px 8px rgba(0, 0, 0, 0.35);
  }
  .card--front { left: 54px; }
  .card--back { left: 630px; }

  .brand-name {
    position: absolute;
    left: 0;
    width: 100%;
    text-align: center;
    font-family: "Cinzel", serif;
    font-weight: 400;
    font-size: 27px;
    letter-spacing: 1px;
    color: var(--gold);
    white-space: nowrap;
  }
  .card--front .brand-name { top: 72px; }
  .card--back .brand-name { top: 112px; }

  .holder {
    position: absolute;
    top: 186px;
    left: 0;
    width: 100%;
    text-align: center;
    color: var(--gold);
    white-space: nowrap;
  }
  .holder__name {
    font-family: "Cinzel", serif;
    font-weight: 700;
    font-size: 17px;
    letter-spacing: 2.5px;
  }
  .holder__title {
    font-family: "Tinos", serif;
    font-size: 13px;
    margin-left: 2px;
  }

  .rule {
    position: absolute;
    left: 0;
    top: 217px;
    width: 100%;
    height: 3px;
    background: var(--gold);
  }
  .contact-band {
    position: absolute;
    left: 0;
    top: 222px;
    width: 100%;
    height: 71px;
    background: var(--maroon);
    font-family: "Tinos", serif;
    font-size: 12.5px;
    line-height: 19px;
    color: var(--gold);
  }
  .contact-col {
    position: absolute;
    top: 16px;
  }
  .contact-col--address { left: 42px; }
  .contact-col--phone { left: 181px; }
  .contact-col--web { left: 334px; }
  .contact-divider {
    position: absolute;
    top: 16px;
    width: 1px;
    height: 40px;
    background: var(--divider);
  }
  .contact-divider--one { left: 170px; }
  .contact-divider--two { left: 321px; }
  .contact-line {
    display: flex;
    align-items: center;
    white-space: nowrap;
  }
  .contact-line svg {
    width: 10px;
    height: 10px;
    margin-right: 5px;
    flex: none;
    fill: var(--gold-soft);
  }

  .web-address {
    position: absolute;
    top: 228px;
    left: 0;
    width: 100%;
    text-align: center;
    font-family: "Tinos", serif;
    font-size: 13px;
    letter-spacing: 2.6px;
    color: #ffffff;
  }
</style>
</head>
<body>
<main class="canvas">

  <section class="card card--front" aria-label="Business card front">
    <p class="brand-name">MARLOW &amp; QUINCE</p>

    <p class="holder">
      <span class="holder__name">YOUR NAME /</span>
      <span class="holder__title">Title</span>
    </p>

    <div class="rule"></div>

    <div class="contact-band">
      <div class="contact-col contact-col--address">
        <p class="contact-line">00, Complex name</p>
        <p class="contact-line">City, State 000 000</p>
      </div>

      <div class="contact-divider contact-divider--one"></div>

      <div class="contact-col contact-col--phone">
        <p class="contact-line">
          <svg viewBox="0 0 10 10" aria-hidden="true"><path d="M2.2 0.6 L3.6 2.6 L2.7 3.6 C3.3 5 4.9 6.6 6.4 7.3 L7.4 6.4 L9.4 7.8 L8.4 9.4 C4.6 9.4 0.6 5.4 0.6 1.6 Z"/></svg>
          +2348105550147
        </p>
        <p class="contact-line">
          <svg viewBox="0 0 10 10" aria-hidden="true"><path d="M3 0.5 H7 A0.8 0.8 0 0 1 7.8 1.3 V8.7 A0.8 0.8 0 0 1 7 9.5 H3 A0.8 0.8 0 0 1 2.2 8.7 V1.3 A0.8 0.8 0 0 1 3 0.5 Z M3.1 1.6 V7.4 H6.9 V1.6 Z"/></svg>
          +2348105550147
        </p>
      </div>

      <div class="contact-divider contact-divider--two"></div>

      <div class="contact-col contact-col--web">
        <p class="contact-line">
          <svg viewBox="0 0 10 10" aria-hidden="true"><path d="M0.8 2 H9.2 V8 H0.8 Z M1.4 2.4 L5 5.3 L8.6 2.4 Z"/></svg>
          info@marlowquince.com
        </p>
        <p class="contact-line">
          <svg viewBox="0 0 10 10" aria-hidden="true"><circle cx="5" cy="5" r="4.3"/><path d="M0.9 4.6 H9.1 V5.4 H0.9 Z" fill="#7a1515"/></svg>
          www.marlowquince.com
        </p>
      </div>
    </div>
  </section>

  <section class="card card--back" aria-label="Business card back">
    <p class="brand-name">MARLOW &amp; QUINCE</p>
    <p class="web-address">www.marlowquince.com</p>
  </section>

</main>
</body>
</html>
```